Belmont Ridge Business Card Design Project

We have recently rebranded and would like to design new business cards that incorporate the corporate logo - double sided cards with corporate logo on one side and contact details on the other

Target Market(s)

Sophisticated and high net worth investors and finance industry professionals

Industry/Entity Type

Funds Management

Contact Information for Business Card

The card should prominently feature the company name and logo. Other details will be standard contact details for each staff member - name, address, phone, email, website

Colors
0054AA
0677BA
7BADD7
CADEEF
E8F1F8

Requirements
Must have
• Double-sided design with one side prominently featuring the corporate logo and the other side with all standard contact details

```html
<!DOCTYPE html>
<html lang="en">
<head>
<meta charset="utf-8">
<title>Belmont Ridge – Business Card</title>
<link rel="stylesheet" href="https://fonts.googleapis.com/css2?family=Tinos:wght@400;700&family=Arimo:wght@400&display=swap">
<style>
  :root {
    --navy: #18467a;
    --ink: #333333;
    --paper: #ffffff;
    --backdrop: #e6e8eb;
  }
  * { margin: 0; padding: 0; box-sizing: border-box; }
  html, body { width: 1200px; height: 1059px; overflow: hidden; }
  body { background: var(--backdrop); position: relative; font-family: "Arimo", Arial, sans-serif; }

  .card { position: absolute; width: 690px; height: 392px; border-radius: 20px; overflow: hidden; }
  .card-front { left: 255px; top: 89px; background: var(--paper); }
  .card-back { left: 255px; top: 569px; background: var(--navy); }

  .brand-name {
    position: absolute; font-family: "Tinos", "Times New Roman", serif; font-weight: 700;
    white-space: nowrap; letter-spacing: 1px;
  }
  .card-front .brand-name { left: 35px; top: 90px; font-size: 36px; color: var(--navy); }
  .card-back .brand-name {
    left: 0; right: 0; top: 190px; text-align: center; font-size: 52px; color: var(--paper);
  }

  .person { position: absolute; right: 35px; top: 157px; text-align: right; }
  .person-name {
    font-family: "Tinos", "Times New Roman", serif; font-weight: 700; font-size: 24px;
    color: var(--navy); line-height: 26px; letter-spacing: 0.3px;
  }
  .person-title { font-size: 16px; color: var(--ink); line-height: 20px; }

  .divider { position: absolute; left: 35px; right: 35px; top: 219px; height: 1px; background: var(--navy); }

  .address { position: absolute; left: 35px; top: 236px; font-size: 16px; line-height: 22px; color: var(--ink); }
  .contacts { position: absolute; left: 35px; top: 284px; list-style: none; }
  .contacts li {
    display: flex; align-items: center; gap: 8px; font-size: 16px; color: var(--ink);
    height: 25.5px;
  }
  .contacts svg { width: 13px; height: 13px; fill: var(--navy); flex: none; }
</style>
</head>
<body>
  <section class="card card-front">
    <div class="brand-name">BELMONT RIDGE</div>

    <div class="person">
      <div class="person-name">DANIEL HAYES</div>
      <div class="person-title">CEO/Founder</div>
    </div>

    <div class="divider"></div>

    <address class="address" style="font-style:normal">
      Po Box 4190 Street Name<br>
      Country Name CD 7321
    </address>

    <ul class="contacts">
      <li>
        <svg viewBox="0 0 16 16" aria-hidden="true"><path d="M3.6 1.2l2.3 2.9-1.3 1.6c.9 2 2.6 3.7 4.6 4.6l1.6-1.3 2.9 2.3-1.4 2.3C7 13.5 2.5 9 1.3 2.6z"/></svg>
        (123) 514-7730
      </li>
      <li>
        <svg viewBox="0 0 16 16" aria-hidden="true"><path d="M0 3h16v1.2L8 9 0 4.2z"/><path d="M0 5.8l8 4.8 8-4.8V13H0z"/></svg>
        info@belmontridge.com
      </li>
      <li>
        <svg viewBox="0 0 16 16" aria-hidden="true"><path d="M8 0a8 8 0 100 16A8 8 0 008 0zm0 1.4c.8 0 1.8 1.8 2.1 4.5H5.9C6.2 3.2 7.2 1.4 8 1.4zM5.8 7.2h4.4v1.6H5.8zm-1.3 0v1.6H1.5a6.6 6.6 0 010-1.6zm7 0h3a6.6 6.6 0 010 1.6h-3zM4.6 5.9H1.9a6.6 6.6 0 013.9-3.8c-.6 1-1 2.3-1.2 3.8zm6.8 0c-.2-1.5-.6-2.8-1.2-3.8a6.6 6.6 0 013.9 3.8zM1.9 10.1h2.7c.2 1.5.6 2.8 1.2 3.8a6.6 6.6 0 01-3.9-3.8zm4 0h4.2c-.3 2.7-1.3 4.5-2.1 4.5s-1.8-1.8-2.1-4.5zm5.5 0h2.7a6.6 6.6 0 01-3.9 3.8c.6-1 1-2.3 1.2-3.8z"/></svg>
        www.belmontridge.com
      </li>
    </ul>
  </section>

  <section class="card card-back">
    <div class="brand-name">BELMONT RIDGE</div>
  </section>
</body>
</html>
```